Veriplume Digital Badge Header/Banner for Nimbleway People Certificaiton

We need a new page header/banner for Veriplume https://www.badgequill.example/ where we have all our digital badges and certificates for our Nimbleway People Coaching https://www.badgequill.example/issuer/48213/credentials

https://www.badgequill.example/group/503118
https://www.badgequill.example/group/514927
https://www.badgequill.example/group/520364

https://www.brightfernpartners.example/

Target Market(s)

HR Professionals

Font styles to use
Sans Serif

```html
<!DOCTYPE html>
<html lang="en">
<head>
<meta charset="utf-8">
<title>Veriplume — Nimbleway People Badges Banner</title>
<link rel="stylesheet" href="https://fonts.googleapis.com/css2?family=Montserrat:wght@400;700&display=swap">
<style>
  :root {
    --page-bg: #ffffff;
    --band-blue: #3d55b8;
    --band-indigo: #4a3fae;
    --band-violet: #7d55cc;
    --inner-navy: #15196b;
    --inner-blue: #2d4aa3;
    --inner-purple: #7a45c4;
    --frame-white: #ffffff;
    --text-white: #ffffff;
  }
  html, body {
    margin: 0;
    padding: 0;
    width: 1200px;
    height: 511px;
    overflow: hidden;
    background: var(--page-bg);
  }
  .banner {
    position: absolute;
    left: 49px;
    top: 108px;
    width: 1101px;
    height: 293px;
    background: linear-gradient(100deg, var(--band-blue) 0%, var(--band-indigo) 50%, var(--band-violet) 100%);
    overflow: hidden;
  }
  .banner-art {
    position: absolute;
    left: 35px;
    top: 29px;
    width: 1031px;
    height: 232px;
    background:
      radial-gradient(ellipse 60% 70% at 50% 0%, var(--inner-navy) 0%, transparent 70%),
      linear-gradient(100deg, var(--inner-blue) 0%, #3a3aa8 45%, var(--inner-purple) 100%);
  }
  .banner-frame {
    position: absolute;
    left: 0;
    top: 0;
    width: 1101px;
    height: 293px;
  }
  .headline {
    position: absolute;
    left: 0;
    width: 1101px;
    margin: 0;
    text-align: center;
    color: var(--text-white);
    font-family: "Montserrat", sans-serif;
    white-space: nowrap;
    text-shadow: 0 1px 3px rgba(10, 10, 60, 0.35);
  }
  .headline-intro {
    top: 59px;
    font-weight: 400;
    font-size: 39px;
    line-height: 40px;
    letter-spacing: 0.32em;
    padding-left: 0.32em;
  }
  .headline-main {
    font-weight: 700;
    font-size: 57px;
    line-height: 58px;
    letter-spacing: 0.005em;
  }
  .headline-line-two { top: 112px; }
  .headline-line-three { top: 174px; }
</style>
</head>
<body>
  <header class="banner">
    <div class="banner-art" role="img" aria-label="Soft collage of certificates and digital badges on a blue to purple network background"></div>
    <svg class="banner-frame" viewBox="0 0 1101 293" aria-hidden="true">
      <path d="M56 26 H1062 a8 8 0 0 1 8 8 V240 a28 28 0 0 1 -28 28 H36 a4 4 0 0 1 -4 -4 V56 a30 30 0 0 1 30 -30 Z"
            fill="none" stroke="var(--frame-white)" stroke-width="7"/>
    </svg>
    <p class="headline headline-intro">WE HAVE ALL OUR</p>
    <h1 class="headline headline-main headline-line-two">DIGITAL BADGES &amp; CERTIFICATES</h1>
    <p class="headline headline-main headline-line-three">FOR OUR NIMBLEWAY PEOPLE</p>
  </header>
</body>
</html>
```